Business Card Design Project

Business Card design based on logo.
Updates

I need business card, letterhead, envelope, and if possible, Powerpoint slide template.

On front of business card: Just logo- and  my name and title:  Harriet Lindqvist, Principal

On reverse-logo and the rest of the contact info:

4871 Quarry Lane
Davis, CA 95618
650-318-2764
hl@brackenstudyworks.example

On letterhead-Just logo at top, at bottom  the rest-very small along the bottom

On PPT slide-just the logo.

I also want to try a few other colors-I like lime/dark grey (not black) but would like to try Sienna, maybe also indigo or bright blue-green.

I forgot to add-

On the business card-switch to vertical on reverse side and put:

Reverse side-switch to vertical and list:

Harriet Lindqvist
Principal
Bracken Study Works, LLC

650-318-2764

4871 Quarry Lane
Davis, CA 95618

Harriet Lindqvist
Principal

650-318-2764

4871 Quarry Lane
Davis, CA 95618

I have another project at the same time-for Stationery. Feel free to submit to that one also.

That one includes letterhead, envelope, PPT slide, folder cover sheet-HL

Industry/Entity Type

Business

Requirements
Must have
• Must use logo-preferably lime green version-with gray, not black or just 2-tone -logo on colored background.

```html
<!DOCTYPE html>
<html lang="en">
<head>
<meta charset="utf-8">
<title>Bracken Study Works – Business Card</title>
<link href="https://fonts.googleapis.com/css2?family=Lato:wght@400;700&display=swap" rel="stylesheet">
<style>
  :root {
    --backdrop: #d9d9d9;
    --card-white: #f4f4f2;
    --lime: #8db43a;
    --charcoal: #4a4a4f;
    --rule: #6a6a6e;
    --paper-band: #ecece8;
  }
  * { box-sizing: border-box; margin: 0; padding: 0; }
  html, body {
    width: 1200px; height: 747px; overflow: hidden;
    background: var(--backdrop);
    font-family: "Lato", sans-serif;
    color: var(--charcoal);
  }
  .stage { position: relative; width: 1200px; height: 747px; }
  .card {
    position: absolute; top: 58px; width: 360px; height: 630px;
    box-shadow: 0 6px 18px rgba(0,0,0,0.18);
  }

  /* Contact side */
  .card--contact { left: 190px; background: var(--card-white); padding: 44px 34px 0 38px; }
  .contact-name { font-size: 24px; font-weight: 400; letter-spacing: 0.5px; text-transform: uppercase; line-height: 1.1; }
  .contact-role, .contact-company { font-size: 16px; line-height: 1.3; }
  .contact-role { margin-top: 4px; }
  .divider { border: 0; border-top: 1.5px solid var(--rule); margin: 18px 0 34px; }
  .contact-list { list-style: none; font-size: 17px; }
  .contact-list li { display: flex; align-items: flex-start; gap: 10px; line-height: 1.35; }
  .contact-list li + li { margin-top: 4px; }
  .contact-list li.contact-address { margin-top: 20px; }
  .contact-list svg { width: 14px; height: 14px; flex: none; margin-top: 4px; fill: var(--lime); }
  .contact-mark {
    position: absolute; left: 38px; bottom: 70px;
    display: flex; align-items: center; gap: 10px;
    font-size: 16px; font-weight: 700; letter-spacing: 1px; text-transform: uppercase;
    color: var(--lime);
  }
  .contact-mark .mark-square { width: 14px; height: 14px; background: var(--lime); }

  /* Brand side */
  .card--brand { left: 650px; background: var(--lime); }
  .brand-square {
    position: absolute; left: 96px; top: 250px; width: 96px; height: 96px;
    background: var(--card-white);
  }
  .brand-name {
    position: absolute; right: 46px; top: 120px; height: 420px;
    writing-mode: vertical-rl; transform: rotate(180deg);
    text-align: center;
    font-size: 38px; font-weight: 700; letter-spacing: 6px; text-transform: uppercase;
    color: var(--charcoal);
  }
</style>
</head>
<body>
<main class="stage">
  <section class="card card--contact" aria-label="Business card, contact side">
    <h1 class="contact-name">Harriet Lindqvist</h1>
    <p class="contact-role">Principal</p>
    <p class="contact-company">Bracken Study Works, LLC</p>
    <hr class="divider">
    <ul class="contact-list">
      <li>
        <svg viewBox="0 0 14 14" aria-hidden="true"><rect x="0" y="0" width="14" height="14" rx="1.5"/><rect x="3" y="2.5" width="8" height="3" fill="#f4f4f2"/><rect x="3" y="7" width="2" height="2" fill="#f4f4f2"/><rect x="6" y="7" width="2" height="2" fill="#f4f4f2"/><rect x="9" y="7" width="2" height="2" fill="#f4f4f2"/></svg>
        <span>650-318-2764</span>
      </li>
      <li>
        <svg viewBox="0 0 14 14" aria-hidden="true"><rect x="0" y="2" width="14" height="10" rx="1"/><path d="M1.5 3.5 L7 8 L12.5 3.5" stroke="#f4f4f2" stroke-width="1.3" fill="none"/></svg>
        <span>hl@brackenstudyworks.example</span>
      </li>
      <li class="contact-address">
        <svg viewBox="0 0 14 14" aria-hidden="true"><path d="M7 0 C3.8 0 2 2.3 2 5 C2 8.5 7 14 7 14 C7 14 12 8.5 12 5 C12 2.3 10.2 0 7 0 Z"/><circle cx="7" cy="5" r="2" fill="#f4f4f2"/></svg>
        <span>4871 Quarry Lane<br>Davis, CA 95618</span>
      </li>
    </ul>
    <div class="contact-mark"><span class="mark-square" aria-hidden="true"></span>Bracken Study Works</div>
  </section>

  <section class="card card--brand" aria-label="Business card, brand side">
    <div class="brand-square" aria-hidden="true"></div>
    <p class="brand-name">Bracken Study Works</p>
  </section>
</main>
</body>
</html>
```